Drug Testing Kit needs a packaging design

I need a professional yet eye catching design for my 5 in 1 drug testing kit.

We call ourselves Coastal Assay Laboratories or "CAL" and am currently running an Ebay business selling Drug Testing Kits. Based in Australia, I am now looking to market my products to local chemists and brach out to the commercial market.

We currently sell a number of different diagnostic tests;Single purchase tests are; THC (Marijuana), Opiates, Amphetamines. We also sell "3 in 1" tests (THC, Amphetamines, MDMA and we sell "5 in 1" tests (THC, COCAINE, Amphetamines, MDMA and Opiates.

I would like to use design that integrates the colours of the individually wrapped items and catches the eye of the customer. I want to market the product to look very professional, almost like it's a medication.
Updates

Measurement changed from ng/ml to μg/L

email to feature on rear 

info@coastalassaylabsonline.com

Target Market(s)

This product will be marketed to Pharmacies and Chemists (Drug Stores) for sale to the general public.

Industry/Entity Type

Business

Requirements
Must have
• Must feature the CAL logo (which is just CAL in font type) somewhere on the packaging.

Must have the Cutoff Limits of the drugs listed for the 5 in 1 test. (THC 50μg/L, COCAINE 300μg/L, AMPHETAMINES 1000μg/L, OPIATES 300μg/L, MDMA 500μg/L(Ecstasy).

The CE approval of the item must be included somewhere on the packaging. ISO13485 ISO9001 ISO14001

Contents 1x Multi Panel Urine Drug Testing Kit, 1x Instruction manual

Email on rear
Nice to have
• The proper chemical names on the front.

'Urine drug tests screen the urine for the presence of a parent drug or its metabolites. Urine is generally considered the best medium to measure in terms of detecting drugs and drug metabolites. Compared to blood, urine offers a longer window of detection that may be one to three days for some drugs and up to 30 days for others. Urine drug testing is by far the most extensively studied and validated process for drug testing. A non-negative (positive) result indicates that the amount of drug / metabolites are above the cutoff limits for the test. '
Should not have
• Nothing unprofessional or suggesting that drug use is bad or not ok. We are not marketing that drug use is illegal or bad. We do not want potential customers to feel guilty when purchasing our items.

```html
<!DOCTYPE html>
<html lang="en">
<head>
<meta charset="utf-8">
<title>CAL 5 in 1 Drug Testing Kit – Packaging</title>
<link rel="stylesheet" href="https://fonts.googleapis.com/css2?family=Archivo+Black&family=Arimo:wght@400;700&family=Open+Sans:wght@600&display=swap">
<style>
  :root{
    --cyan:#19c9f2;
    --cyan-light:#8ee9fb;
    --cyan-mid:#4cc3ee;
    --blue:#0b1fd6;
    --ink:#0a0a0a;
    --white:#ffffff;
    --gold:#c9a65a;
    --logo:#22d6ef;
  }
  *{margin:0;padding:0;box-sizing:border-box}
  html,body{width:1200px;height:1000px;overflow:hidden}
  body{
    position:relative;
    font-family:"Arimo",Arial,sans-serif;
    background:radial-gradient(ellipse at 55% 40%,#e6fbff 0%,#9eeefd 45%,#3fd5f6 100%);
  }
  .abs{position:absolute}

  .flap{background:var(--cyan)}
  .flap-inner{background:var(--cyan-light)}
  .panel{overflow:hidden}
  .panel.front{
    background:
      radial-gradient(ellipse 60% 35% at 70% 30%,rgba(255,255,255,.95),transparent 70%),
      radial-gradient(ellipse 70% 40% at 30% 75%,rgba(90,200,240,.55),transparent 70%),
      linear-gradient(180deg,#9fe3f8 0%,#f2fbff 40%,#bfe9f9 75%,#ffffff 100%);
  }
  .panel.back{
    background:
      radial-gradient(ellipse 45% 18% at 75% 10%,rgba(255,255,255,.85),transparent 70%),
      radial-gradient(ellipse 40% 25% at 20% 80%,rgba(255,255,255,.6),transparent 70%),
      linear-gradient(180deg,#8fdcf5 0%,#c6f0fc 14%,#5cc9ef 32%,#44bdeb 52%,#6fcff1 72%,#d8f4fd 88%,#ffffff 100%);
  }
  .side{background:var(--cyan)}

  .five{font-family:"Arimo",Arial,sans-serif;font-weight:700;color:var(--blue);line-height:1;white-space:nowrap}
  .five .in{font-size:.62em}
  .five-box{background:var(--white);display:flex;align-items:center;justify-content:center}

  .title{font-family:"Archivo Black","Arial Black",sans-serif;color:var(--ink);white-space:nowrap;line-height:1}
  .title.white{color:var(--white);text-shadow:1px 2px 2px rgba(0,0,0,.45)}

  .drug-list{list-style:none;font-weight:700;font-size:18px;color:var(--ink);line-height:22px}
  .drug-list li::before{content:"•";color:var(--white);margin-right:10px}

  .claim{font-weight:700;font-size:15px;color:var(--ink);padding:1px 6px;
    background:linear-gradient(90deg,#ffffff 0%,#e8fbff 45%,#3fe0fa 100%);width:128px}

  .contents{font-size:15px;color:var(--ink);line-height:18px}
  .contents h4{font-weight:400;text-decoration:underline;font-size:15px}

  .logo{font-family:"Arimo",Arial,sans-serif;font-weight:700;font-size:34px;color:var(--logo);letter-spacing:1px}

  .info-box{border:1.5px solid var(--white);color:var(--white);font-size:12px;line-height:15px;text-align:justify;padding:12px 16px;text-shadow:0 0 2px rgba(0,70,120,.35)}
  .cutoffs{color:var(--white);font-size:12.4px;line-height:15px;text-shadow:0 0 2px rgba(0,70,120,.3)}
  .cutoffs h4{font-weight:400;font-size:12.4px;border-bottom:1px solid var(--white);display:inline-block;padding-right:22px;margin-bottom:8px}
  .certs{color:var(--white);font-weight:700;font-size:11px;display:flex;align-items:center;gap:6px}
  .cert-mark{width:14px;height:10px;border:1.5px solid var(--white);border-radius:2px}

  .vertical-up{writing-mode:vertical-rl;transform:rotate(180deg)}
  .vertical-down{writing-mode:vertical-rl}
  .side-title{font-family:"Archivo Black","Arial Black",sans-serif;color:var(--white);font-size:34px;white-space:nowrap}

  .sheet-label{font-family:"Open Sans",Arial,sans-serif;font-weight:600;font-size:42px;color:var(--white)}
  .product-visual{background:linear-gradient(160deg,#1b2f9a 0%,#2b3fa8 30%,#f08a2a 45%,#ffffff 55%,#f4f6f8 80%,#dfe6ea 100%);border-radius:4px;transform:rotate(-4deg)}
</style>
</head>
<body>

  <div class="abs flap" style="left:80px;top:45px;width:467px;height:117px"></div>
  <div class="abs flap-inner" style="left:80px;top:93px;width:467px;height:69px;display:flex;align-items:center;justify-content:center;gap:26px;transform:rotate(180deg)">
    <div class="five-box" style="width:96px;height:52px"><span class="five" style="font-size:38px">5<span class="in">in</span>1</span></div>
    <span class="title" style="font-size:26px;color:var(--blue)">Drug Testing Kit</span>
  </div>

  <section class="abs panel front" style="left:48px;top:162px;width:499px;height:676px">
    <div class="abs side" style="left:0;top:0;width:32px;height:560px"></div>
    <div class="abs" style="left:92px;top:24px;background:var(--cyan-light);padding:0 4px">
      <span class="five" style="font-size:50px">5<span class="in">in</span>1</span>
    </div>
    <h1 class="abs title" style="left:92px;top:88px;font-size:37px">Drug Testing Kit</h1>
    <ul class="abs drug-list" style="left:88px;top:144px">
      <li>AMPHETAMINES</li><li>COCAINE</li><li>MARIJUANA (THC)</li><li>OPIATES</li><li>MDMA</li>
    </ul>
    <div class="abs product-visual" role="img" aria-label="Wrapped drug test pouch beside a five-panel urine test card" style="left:74px;top:272px;width:340px;height:160px"></div>
    <div class="abs claim" style="left:90px;top:458px">Easy to use</div>
    <div class="abs claim" style="left:90px;top:482px">99% Accuracy</div>
    <div class="abs claim" style="left:90px;top:505px">Fast Results</div>
    <svg class="abs" style="left:0;top:540px" width="499" height="136" viewBox="0 0 499 136">
      <path d="M0 30 C60 5 140 5 260 40 C360 70 430 90 499 96 L499 136 L0 136 Z" fill="#fff"/>
      <path d="M0 30 C60 5 140 5 260 40 C360 70 430 90 499 96" fill="none" stroke="var(--gold)" stroke-width="3"/>
    </svg>
    <div class="abs contents" style="left:220px;top:562px">
      <h4>Contents</h4>
      <p>1x Multi Panel Drug Testing Kit</p>
      <p>1x Instruction Manual</p>
    </div>
    <div class="abs logo" style="left:55px;top:608px">CAL</div>
  </section>

  <div class="abs side" style="left:547px;top:108px;width:70px;height:800px"></div>
  <div class="abs flap-inner" style="left:547px;top:108px;width:70px;height:54px"></div>
  <div class="abs vertical-up side-title" style="left:560px;top:235px;height:360px;text-align:center">Drug Testing Kit</div>
  <div class="abs five-box" style="left:547px;top:620px;width:70px;height:140px">
    <span class="five vertical-up" style="font-size:42px">5<span class="in">in</span>1</span>
  </div>

  <section class="abs panel back" style="left:617px;top:162px;width:466px;height:676px">
    <div class="abs certs" style="right:56px;top:24px"><span class="cert-mark"></span>ISO13485 ISO9001 ISO14001</div>
    <div class="abs" style="left:58px;top:72px;background:var(--cyan-light);padding:0 4px">
      <span class="five" style="font-size:50px">5<span class="in">in</span>1</span>
    </div>
    <h2 class="abs title white" style="left:58px;top:135px;font-size:35px">Drug Testing Kit</h2>
    <p class="abs info-box" style="left:55px;top:220px;width:355px;height:168px">Urine is generally considered the best medium to measure in terms of detecting drugs and drug metabolites. Compared to blood, urine offers a longer window of detection that may be one to three days for some drugs and up to 30 days for others. Urine drug testing is by far the most extensively studied and validated process for drug testing. A non-negative (positive) result indicates that the amount of drug / metabolites are above the cutoff limits for the test.</p>
    <div class="abs cutoffs" style="left:56px;top:433px">
      <h4>Cutoff Limits of the drugs</h4>
      <p>THC : 50ng/ml</p>
      <p>COCAINE : 300ng/ml</p>
      <p>AMPHETAMINES : 1000ng/ml</p>
      <p>OPIATES : 300ng/ml</p>
      <p>MDMA : 500ng/ml (Ecstasy)</p>
    </div>
    <svg class="abs" style="left:0;top:540px" width="466" height="136" viewBox="0 0 466 136">
      <path d="M0 20 C90 30 150 110 260 110 C350 110 420 60 466 20 L466 136 L0 136 Z" fill="#fff"/>
      <path d="M0 20 C90 30 150 110 260 110 C350 110 420 60 466 20" fill="none" stroke="var(--gold)" stroke-width="3"/>
    </svg>
    <div class="abs logo" style="left:38px;top:606px">CAL</div>
  </section>

  <div class="abs flap" style="left:617px;top:838px;width:466px;height:117px"></div>
  <div class="abs" style="left:617px;top:838px;width:466px;height:70px;background:var(--cyan);display:flex;align-items:center;padding-left:50px;gap:22px">
    <div class="five-box" style="width:96px;height:50px"><span class="five" style="font-size:38px">5<span class="in">in</span>1</span></div>
    <span class="title" style="font-size:24px;color:var(--white)">Drug Testing Kit</span>
  </div>

  <div class="abs side" style="left:1083px;top:105px;width:70px;height:800px"></div>
  <div class="abs five-box" style="left:1083px;top:242px;width:70px;height:140px">
    <span class="five vertical-down" style="font-size:42px">5<span class="in">in</span>1</span>
  </div>
  <div class="abs vertical-down side-title" style="left:1096px;top:405px;height:360px">Drug Testing Kit</div>

  <div class="abs sheet-label" style="left:175px;top:892px">Full View</div>
</body>
</html>
```